Building company needs a letterhead design

I'm after a modern but professional letter head.
Must have the below details:
- Logo
- Website - TARVELLGROUP.COM.AU
- Email - INFO@TARVELLGROUP.COM.AU
- Office - 03 57263018
- Mobile number - 0418536294
- ABN - 47 315 962 108
...........................................................................................................................................................................................................................
- Logo
- Office - 03 57263018
- ABN - 47 315 962 108

Target Market(s)

.

Industry/Entity Type

Construction Company

Font styles to use
Sans Serif

Requirements
Must have
• Must have the below details:
• - Logo
• - Website - TARVELLGROUP.COM.AU
• - Email - INFO@TARVELLGROUP.COM.AU
• - Office - 03 57263018
• - Mobile number - 0418536294
• - ABN - 47 315 962 108
Nice to have
• .
Should not have
• .

```html
<!DOCTYPE html>
<html lang="en">
<head>
<meta charset="utf-8">
<title>Tarvell Building Group – Letterhead</title>
<link rel="stylesheet" href="https://fonts.googleapis.com/css2?family=Source+Sans+3:wght@400;700&display=swap">
<style>
  :root {
    --page-bg: #e9e7e4;
    --paper: #ffffff;
    --brand-yellow: #fbb416;
    --brand-grey: #55565a;
    --rule-grey: #6d6e72;
    --text-grey: #4a4a4d;
    --footer-rule: #c9c9cb;
  }
  * { box-sizing: border-box; margin: 0; padding: 0; }
  html, body {
    width: 1186px;
    height: 1200px;
    overflow: hidden;
    background: var(--page-bg);
    font-family: "Source Sans 3", Arial, sans-serif;
  }
  .letterhead {
    position: absolute;
    left: 190px;
    top: 30px;
    width: 806px;
    height: 1140px;
    background: var(--paper);
    box-shadow: 0 2px 10px rgba(0,0,0,0.18);
    overflow: hidden;
  }
  .side-band {
    position: absolute;
    left: 0;
    top: 0;
    width: 100px;
    height: 100%;
    background: var(--brand-yellow);
  }
  .side-rule {
    position: absolute;
    left: 108px;
    top: 0;
    width: 2px;
    height: 100%;
    background: var(--rule-grey);
  }
  .brand {
    position: absolute;
    left: 72px;
    top: 38px;
    display: flex;
    align-items: center;
    gap: 14px;
  }
  .brand-square {
    width: 64px;
    height: 64px;
    background: var(--brand-grey);
    border: 5px solid var(--paper);
  }
  .brand-name {
    font-weight: 700;
    font-size: 30px;
    line-height: 1;
    letter-spacing: 1.5px;
    color: var(--brand-grey);
    text-transform: uppercase;
  }
  .contact-footer {
    position: absolute;
    left: 118px;
    bottom: 58px;
    display: flex;
    align-items: flex-end;
    gap: 18px;
    font-size: 12.5px;
    color: var(--text-grey);
    line-height: 1.6;
  }
  .contact-col { display: flex; flex-direction: column; }
  .contact-divider {
    width: 1px;
    height: 46px;
    background: var(--footer-rule);
  }
  .contact-item { display: flex; align-items: center; gap: 5px; }
  .contact-item svg { width: 10px; height: 10px; flex: none; }
  .contact-email { text-transform: lowercase; }
</style>
</head>
<body>
  <main class="letterhead">
    <div class="side-band"></div>
    <div class="side-rule"></div>

    <header class="brand">
      <span class="brand-square"></span>
      <span class="brand-name">Tarvell Building Group</span>
    </header>

    <footer class="contact-footer">
      <div class="contact-col">
        <span class="contact-item">
          <svg viewBox="0 0 10 10"><circle cx="5" cy="5" r="5" fill="#fbb416"/><path d="M3 2.5 L4.2 2.5 L4.6 4 L4 4.5 Q4.8 6 6 6.4 L6.5 5.8 L8 6.2 L8 7.4 Q5 7.8 3 4.8 Z" fill="#fff"/></svg>
          03 57263018
        </span>
        <span class="contact-item">
          <svg viewBox="0 0 10 10"><rect x="2.5" y="0.5" width="5" height="9" rx="1" fill="#fbb416"/><rect x="3.5" y="1.8" width="3" height="5" fill="#fff"/></svg>
          0418536294
        </span>
        <span class="contact-item">ABN: 47 315 962 108</span>
      </div>
      <span class="contact-divider"></span>
      <div class="contact-col">
        <span class="contact-item">
          <svg viewBox="0 0 10 10"><circle cx="5" cy="5" r="5" fill="#fbb416"/><path d="M0.5 5 H9.5 M5 0.5 Q2.5 5 5 9.5 M5 0.5 Q7.5 5 5 9.5" stroke="#fff" stroke-width="0.8" fill="none"/></svg>
          www.tarvellgroup.com.au
        </span>
        <span class="contact-item contact-email">
          <svg viewBox="0 0 10 10"><rect x="0.5" y="2" width="9" height="6.5" rx="1" fill="#fbb416"/><path d="M1 2.5 L5 5.8 L9 2.5" stroke="#fff" stroke-width="0.9" fill="none"/></svg>
          info@tarvellgroup.com.au
        </span>
      </div>
    </footer>
  </main>
</body>
</html>
```